Varnik Holdings — Business Card Design Brief
Overview
Design a double-sided business card for Varnik Holdings that highlights our two service arms: Varnik Communications (telecommunications) and Varnik Energy (business energy solutions). The card should feel smart and stand out when handed to clients.

Objectives
Showcase our areas of specialty clearly.
Reflect the overall Varnik / Varnik Holdings brand while acknowledging both arms.
Explore using both logos (Communications + Energy) or one unified logo, depending on the design.

Deliverables
One double-sided business card design (front + back).

Content & Copy
Front (preferred): Logo: Varnik / Varnik Holdings
Descriptor: Business Communications | Business Energy
Back:My contact details and company details
Core products: Business Mobile • Telephony • Internet • Business Energy Solutions

Brand & Visual Direction
We have a group logo currently tailored more toward telecoms, plus a separate Varnik Energy logo.
Please explore layouts that use both logos or just one, whichever works best.
Color: I wouldn't mind seeing an option using our the Blue/Purple gradient from our website (varnik-example.co.uk), but also open to non-gradient approaches and other colours..

Overall look: Smart, modern, and distinctive.
Format & Print Specs
Double-sided business card format. (Use a standard size

Must-Haves
Front: Varnik wording or Varnik Holdings wording with atleast 1 logo also on front “Business Communications | Business Energy.”

Back: Contact + company details and core products.
A design that stands out while remaining professional.

Nice-to-Have Options
A gradient version using our site’s Blue/Purple gradient.
A non-gradient version.
A dual-logo treatment versus a single-logo treatment.

Thanks
Owen

```html
<!DOCTYPE html>
<html lang="en">
<head>
<meta charset="utf-8">
<title>Varnik Holdings — Business Card</title>
<link href="https://fonts.googleapis.com/css2?family=Arimo:wght@400;700&display=swap" rel="stylesheet">
<style>
  :root {
    --backdrop: #dcdcdc;
    --navy: #1b1464;
    --green: #7ac31f;
    --green-ring: #3faa35;
    --blue-ring: #1e63d6;
    --stripe-dark: #1b5fd0;
    --stripe-light: #16b4e6;
    --white: #ffffff;
    --back-top: #0cb3e3;
    --back-bottom: #0a58d4;
  }
  * { box-sizing: border-box; margin: 0; padding: 0; }
  html, body { width: 1200px; height: 1200px; overflow: hidden; }
  body {
    background: var(--backdrop);
    font-family: "Arimo", Arial, sans-serif;
    position: relative;
  }
  .card {
    position: absolute;
    width: 688px;
    height: 393px;
    overflow: hidden;
  }
  .card--front { left: 267px; top: 159px; background: var(--white); }
  .card--back {
    left: 262px; top: 653px;
    background: linear-gradient(180deg, var(--back-top) 0%, var(--back-bottom) 100%);
  }

  /* front: brand row */
  .brand-row {
    position: absolute; left: 0; top: 0; width: 100%; height: 214px;
    display: flex; justify-content: center; align-items: center; gap: 70px;
  }
  .brand { display: flex; align-items: center; gap: 14px; }
  .brand__dot {
    width: 46px; height: 46px; border-radius: 50%;
    border: 7px solid var(--green-ring);
  }
  .brand__dot--blue { border-color: var(--blue-ring); }
  .brand__name {
    font-weight: 700; font-size: 54px; letter-spacing: 1px;
    color: var(--navy); line-height: 1;
  }

  .stripe { position: absolute; left: 0; width: 100%; height: 3px; }
  .stripe--dark { top: 214px; background: var(--stripe-dark); }
  .stripe--light { top: 217px; background: var(--stripe-light); }

  .info-panel {
    position: absolute; left: 0; top: 222px; width: 100%; height: 171px;
    background: var(--navy); color: var(--white);
  }
  .person {
    position: absolute; right: 346px; top: 26px; text-align: right;
    font-size: 16px; line-height: 21px;
  }
  .person__name {
    color: var(--green); font-weight: 700; font-size: 29px; line-height: 32px;
    letter-spacing: 0.5px; margin-bottom: 1px;
  }
  .divider {
    position: absolute; left: 359px; top: 25px; width: 1px; height: 78px;
    background: var(--white);
  }
  .contacts {
    position: absolute; left: 376px; top: 27px; list-style: none;
    font-size: 16px; line-height: 20.5px;
  }
  .contacts li { display: flex; align-items: center; gap: 9px; }
  .contacts svg { width: 14px; height: 14px; flex: none; }
  .products {
    position: absolute; left: 0; bottom: 17px; width: 100%;
    text-align: center; font-size: 17.5px;
  }

  /* back */
  .arm {
    position: absolute; top: 118px; width: 290px;
    display: flex; flex-direction: column; align-items: center;
    color: var(--white);
  }
  .arm--comms { left: 61px; }
  .arm--energy { left: 337px; }
  .arm__mark { display: flex; align-items: center; gap: 12px; height: 120px; }
  .arm__dot {
    width: 44px; height: 44px; border-radius: 50%;
    border: 6px solid var(--white);
  }
  .arm__name { font-weight: 700; font-size: 46px; letter-spacing: 1px; line-height: 1; }
  .arm__label { margin-top: 20px; font-size: 17px; letter-spacing: 0.2px; }
  .back-divider {
    position: absolute; left: 345px; top: 114px; width: 1px; height: 167px;
    background: rgba(255,255,255,0.8);
  }
</style>
</head>
<body>

<section class="card card--front" aria-label="Card front">
  <div class="brand-row">
    <div class="brand">
      <span class="brand__dot"></span>
      <span class="brand__name">VARNIK</span>
    </div>
    <div class="brand">
      <span class="brand__dot brand__dot--blue"></span>
      <span class="brand__name">VARNIK</span>
    </div>
  </div>
  <div class="stripe stripe--dark"></div>
  <div class="stripe stripe--light"></div>

  <div class="info-panel">
    <div class="person">
      <p class="person__name">DANIEL BROOKS</p>
      <p>President</p>
      <p>412 Alder Court</p>
      <p>Northfield, Canada 20915</p>
    </div>
    <div class="divider"></div>
    <ul class="contacts">
      <li>
        <svg viewBox="0 0 14 14" aria-hidden="true"><path fill="#7ac31f" d="M3 1l2.2 2.6-1.1 1.6c.8 1.7 2 2.9 3.7 3.7l1.6-1.1L12 10l-1.2 2.4C6 12.4 1.6 8 1.6 3.2z"/></svg>
        <span>555-014-2290</span>
      </li>
      <li>
        <svg viewBox="0 0 14 14" aria-hidden="true"><rect x="3.5" y="0.8" width="7" height="12.4" rx="1.2" fill="none" stroke="#7ac31f" stroke-width="1.6"/><circle cx="7" cy="11" r="0.8" fill="#7ac31f"/></svg>
        <span>555-017-6631</span>
      </li>
      <li>
        <svg viewBox="0 0 14 14" aria-hidden="true"><rect x="1" y="3" width="12" height="8.5" fill="#7ac31f"/><path d="M1 3l6 5 6-5" fill="none" stroke="#1b1464" stroke-width="1.2"/></svg>
        <span>info@VARNIK-EXAMPLE.com</span>
      </li>
      <li>
        <svg viewBox="0 0 14 14" aria-hidden="true"><circle cx="7" cy="7" r="6" fill="#7ac31f"/><path d="M3 5c2 0 2 2 3 3s0 3 1 4M8 2c0 2 2 2 3 3" fill="none" stroke="#1b1464" stroke-width="1.2"/></svg>
        <span>www.VARNIK-EXAMPLE.com</span>
      </li>
    </ul>
    <p class="products">Business Mobile&nbsp; •&nbsp; Telephony&nbsp; •&nbsp; Internet&nbsp; •&nbsp; Business Energy Solutions</p>
  </div>
</section>

<section class="card card--back" aria-label="Card back">
  <div class="arm arm--comms">
    <div class="arm__mark">
      <span class="arm__dot"></span>
      <span class="arm__name">VARNIK</span>
    </div>
    <p class="arm__label">BUSINESS COMMUNICATIONS</p>
  </div>
  <div class="back-divider"></div>
  <div class="arm arm--energy">
    <div class="arm__mark">
      <span class="arm__dot"></span>
      <span class="arm__name">VARNIK</span>
    </div>
    <p class="arm__label">BUSINESS ENERGY</p>
  </div>
</section>

</body>
</html>
```